Buch-/eBook-Cover für Sachbuch gesucht
Zielgruppe
We're selfpublishing nonfiction books. Interested are adults - mostly man (age range: 25-50) - who want to learn more about leadership at their workplaces.
Aufgabenstellung
The design should be clean and simple, title easy to read, good color contrast (the cover has to stand out from an white background).

```html
<!DOCTYPE html>
<html lang="en">
<head>
<meta charset="utf-8">
<title>Leadership – Book Cover</title>
<link rel="stylesheet" href="https://fonts.googleapis.com/css2?family=Exo+2:wght@600;700;800&display=swap">
<style>
  :root {
    --page-bg: #f2f2f2;
    --title-red: #d12127;
    --title-white: #ffffff;
    --subtitle-ink: #141210;
    --author-white: #ffffff;
    --sky-top: #8c8273;
    --sky-gold: #e6b46c;
    --sun-glow: #fbe2a6;
    --city-amber: #9a6a3a;
    --ground-dark: #2e2017;
    --ledge-dark: #1b120d;
  }
  * { margin: 0; padding: 0; box-sizing: border-box; }
  html, body {
    width: 996px;
    height: 1200px;
    overflow: hidden;
    background: var(--page-bg);
  }
  .canvas {
    position: relative;
    width: 996px;
    height: 1200px;
  }
  .cover {
    position: absolute;
    left: 89px;
    top: 0;
    width: 818px;
    height: 1200px;
    overflow: hidden;
  }
  .cover-scene {
    position: absolute;
    inset: 0;
    background:
      radial-gradient(ellipse 260px 220px at 620px 580px, var(--sun-glow) 0%, rgba(251,226,166,0) 100%),
      linear-gradient(180deg,
        var(--sky-top) 0%,
        var(--sky-gold) 32%,
        var(--sky-gold) 48%,
        var(--city-amber) 68%,
        var(--ground-dark) 86%,
        var(--ledge-dark) 100%);
  }
  .title-band {
    position: absolute;
    left: 27px;
    top: 39px;
    width: 772px;
    height: 120px;
    background: var(--title-red);
    display: flex;
    align-items: center;
    justify-content: center;
  }
  .title {
    font-family: "Exo 2", sans-serif;
    font-weight: 800;
    font-size: 112px;
    line-height: 1;
    color: var(--title-white);
    letter-spacing: 1px;
    margin-top: 4px;
  }
  .subtitle {
    position: absolute;
    left: 0;
    right: 0;
    top: 162px;
    text-align: center;
    font-family: "Exo 2", sans-serif;
    font-weight: 700;
    font-size: 45px;
    line-height: 54px;
    color: var(--subtitle-ink);
  }
  .author {
    position: absolute;
    left: 0;
    right: 0;
    top: 1134px;
    text-align: center;
    font-family: "Exo 2", sans-serif;
    font-weight: 700;
    font-size: 29px;
    color: var(--author-white);
  }
</style>
</head>
<body>
  <div class="canvas">
    <div class="cover">
      <div class="cover-scene" role="img" aria-label="Photo of a man in a dark suit seen from behind, standing on a rooftop terrace and looking over a city skyline, river and mountains at golden sunset"></div>
      <div class="title-band">
        <h1 class="title">LEADERSHIP</h1>
      </div>
      <p class="subtitle">Fostering Growth and<br>Inspiring Excellence</p>
      <p class="author">DANIEL HARTLEY</p>
    </div>
  </div>
</body>
</html>
```